Stationery Set for Velmora Company

I need to create full stationery design for my company; Business Cards, Envelops, Letter Heads, Calendar.
In the letter head and Envelops... only contact information and website links.
Our company is a Service Management company with different domains of innovative services including Technology Service Management, Education Services, Outsourcing Management, Events Management.
I need a modern and innovative design specially for the business card. I some transparent designs and I like it, but don't limit your innovation to what I mentioned. Sky is limit for your innovation.

Target Market(s)

Middle East & Africa

Industry/Entity Type

Business Management

Colors
34a7d8
0355a3
85acd3
86cae7
cee9f5
cfdeed
e4daeb
f3f1f8
ecf7fb

Requirements
Must have
• Name, Title, Email, Mobile
Nice to have
• We have multiple locations in USA, KSA, EGY, so I need ideas about how to include all contact details maybe QR / Barcode or something else.
• Please see our locations and contact information: www.brightvelmora.example
Should not have
• Too much text

```html
<!DOCTYPE html>
<html lang="en">
<head>
<meta charset="utf-8">
<title>Velmora Company – Business Card</title>
<link rel="stylesheet" href="https://fonts.googleapis.com/css2?family=Open+Sans:wght@400;600;700&display=swap">
<style>
  :root {
    --brand-blue: #3f69b0;
    --brand-grey: #bcb7b8;
    --ink: #1a1a1a;
    --paper: #ffffff;
    --backdrop: #e4e4e4;
  }
  * { margin: 0; padding: 0; box-sizing: border-box; }
  html, body {
    width: 1105px; height: 1200px; overflow: hidden;
    background: var(--backdrop);
    font-family: "Open Sans", Arial, sans-serif;
  }
  .card {
    position: absolute; left: 112px;
    width: 880px; height: 502px; overflow: hidden;
  }
  .card-front { top: 58px; background: var(--paper); }
  .card-back { top: 640px; background: var(--brand-blue); }

  .brand {
    position: absolute; display: flex; align-items: center; gap: 12px;
    font-weight: 700; letter-spacing: -1px; line-height: 1;
  }
  .card-front .brand { right: 56px; top: 70px; font-size: 62px; color: var(--brand-blue); }
  .card-front .brand-dot { width: 20px; height: 20px; border-radius: 50%; background: var(--brand-grey); }
  .card-back .brand { left: 0; right: 0; justify-content: center; top: 162px; font-size: 72px; color: var(--paper); }
  .card-back .brand-dot { width: 24px; height: 24px; border-radius: 50%; background: var(--brand-grey); }

  .holder { position: absolute; left: 35px; top: 182px; }
  .holder-name { font-size: 33px; font-weight: 600; color: var(--brand-blue); line-height: 1.2; }
  .holder-title { font-size: 26px; color: var(--ink); line-height: 1.25; }

  .address-band {
    position: absolute; left: 0; right: 0; top: 307px; bottom: 0;
    background: var(--brand-blue);
  }
  .accent-strip { position: absolute; left: 0; top: 307px; }

  .office { position: absolute; color: var(--paper); font-size: 22px; line-height: 32px; }
  .office-label { font-weight: 700; }
  .office-saudi { left: 35px; top: 324px; }
  .office-usa { right: 60px; top: 352px; text-align: right; }

  .contact-list {
    position: absolute; left: 0; right: 0; top: 352px;
    color: var(--paper); font-size: 22px; line-height: 34px; text-align: center;
  }
  .contact-row { display: flex; justify-content: center; align-items: center; gap: 6px; }
  .contact-item { display: inline-flex; align-items: center; gap: 5px; }
  .icon { width: 20px; height: 20px; fill: var(--paper); flex: none; }
</style>
</head>
<body>

<section class="card card-front">
  <div class="brand"><span>Velmora</span><span class="brand-dot"></span></div>

  <div class="holder">
    <p class="holder-name">Omar Haddad</p>
    <p class="holder-title">CEO/Founder</p>
  </div>

  <div class="address-band"></div>
  <svg class="accent-strip" width="880" height="22" viewBox="0 0 880 22" aria-hidden="true">
    <polygon points="566,0 880,0 880,20 557,20" fill="#bcb7b8"/>
  </svg>

  <address class="office office-saudi" style="font-style:normal">
    <span class="office-label">SAUDI</span><br>
    Riyadh, Al Nakheel,<br>
    Qasr Al Noor St.<br>
    Almaha Towers<br>
    Block 4C 3rd Floor C12, C14
  </address>

  <address class="office office-usa" style="font-style:normal">
    <span class="office-label">USA</span><br>
    418 Harbor Crest Lane<br>
    4th Floor Lakeview City<br>
    CA 90017 US
  </address>
</section>

<section class="card card-back">
  <div class="brand"><span>Velmora</span><span class="brand-dot"></span></div>

  <div class="contact-list">
    <div class="contact-row">
      <span class="contact-item">
        <svg class="icon" viewBox="0 0 24 24" aria-hidden="true"><path d="M6.6 10.8a15.1 15.1 0 0 0 6.6 6.6l2.2-2.2c.3-.3.7-.4 1-.2 1.1.4 2.3.6 3.6.6.6 0 1 .4 1 1V20c0 .6-.4 1-1 1A17 17 0 0 1 3 4c0-.6.4-1 1-1h3.5c.6 0 1 .4 1 1 0 1.3.2 2.5.6 3.6.1.3 0 .7-.2 1z"/></svg>
        +1.5550147820 (USA)
      </span>
      <span class="contact-item">
        <svg class="icon" viewBox="0 0 24 24" aria-hidden="true"><path d="M6.6 10.8a15.1 15.1 0 0 0 6.6 6.6l2.2-2.2c.3-.3.7-.4 1-.2 1.1.4 2.3.6 3.6.6.6 0 1 .4 1 1V20c0 .6-.4 1-1 1A17 17 0 0 1 3 4c0-.6.4-1 1-1h3.5c.6 0 1 .4 1 1 0 1.3.2 2.5.6 3.6.1.3 0 .7-.2 1z"/></svg>
        +966 90000 12 34 (Saudi)
      </span>
    </div>
    <div class="contact-row">
      <span class="contact-item">
        <svg class="icon" viewBox="0 0 24 24" aria-hidden="true"><path d="M7 1h10a2 2 0 0 1 2 2v18a2 2 0 0 1-2 2H7a2 2 0 0 1-2-2V3a2 2 0 0 1 2-2zm0 3v14h10V4zm5 15.2a1.1 1.1 0 1 0 0 2.2 1.1 1.1 0 0 0 0-2.2z"/></svg>
        +1.5550147820
      </span>
      <span class="contact-item">
        <svg class="icon" viewBox="0 0 24 24" aria-hidden="true"><path d="M2 5h20v14H2zm2 2v.4l8 5.2 8-5.2V7zm0 2.8V17h16V9.8l-8 5.2z"/></svg>
        info@brightvelmora.example
      </span>
      <span class="contact-item">
        <svg class="icon" viewBox="0 0 24 24" aria-hidden="true"><path d="M12 2a10 10 0 1 0 0 20 10 10 0 0 0 0-20zm6.9 6h-3a15.6 15.6 0 0 0-1.3-3.6A8 8 0 0 1 18.9 8zM12 4c.8 1.2 1.5 2.5 1.9 4h-3.8c.4-1.5 1.1-2.8 1.9-4zM4.3 14a8.2 8.2 0 0 1 0-4h3.4a16.5 16.5 0 0 0 0 4zm.8 2h3a15.6 15.6 0 0 0 1.3 3.6A8 8 0 0 1 5.1 16zm3-8h-3a8 8 0 0 1 4.3-3.6C8.8 5.5 8.4 6.7 8.1 8zM12 20c-.8-1.2-1.5-2.5-1.9-4h3.8c-.4 1.5-1.1 2.8-1.9 4zm2.3-6H9.7a14.7 14.7 0 0 1 0-4h4.6a14.7 14.7 0 0 1 0 4zm.3 5.6c.6-1.1 1-2.3 1.3-3.6h3a8 8 0 0 1-4.3 3.6zm1.7-5.6a16.5 16.5 0 0 0 0-4h3.4a8.2 8.2 0 0 1 0 4z"/></svg>
        www.brightvelmora.example
      </span>
    </div>
  </div>
</section>

</body>
</html>
```